Business Card Design for Occupational Medicine Start Up Company

We need to design a professional business card. We are a healthcare company providing occupational medicine services to blue collar industries. We are professional, efficient and high quality service providers.

Target Market(s)

Blue Collar Industry: Shipbuilding, Ports, Trucking Companies; The Executives and Safety Officers for these companies

Industry/Entity Type

Healthcare

Contact Information for Business Card

Logo, Name, Title, Email, Phone

Other font styles liked:
• Please match our Brand Guide

Requirements
Must have
• Our Company Colors and Logo

```html
<!DOCTYPE html>
<html lang="en">
<head>
<meta charset="utf-8">
<title>Crewline Health – Business Card</title>
<link href="https://fonts.googleapis.com/css2?family=Montserrat:wght@400;500;600;700&display=swap" rel="stylesheet">
<style>
  :root {
    --backdrop: #2b2b2b;
    --navy: #33307a;
    --sky: #2fa0dc;
    --amber: #f0ab3c;
    --paper: #f6f6f4;
    --white: #ffffff;
    --ink: #2f2c72;
  }
  * { margin: 0; padding: 0; box-sizing: border-box; }
  html, body {
    width: 1200px; height: 1200px; overflow: hidden;
    background: var(--backdrop);
    font-family: "Montserrat", Arial, sans-serif;
  }
  .card {
    position: absolute;
    width: 594px; height: 348px;
    border-radius: 20px;
    overflow: hidden;
  }
  .card-front { left: 298px; top: 200px; background: var(--navy); }
  .card-back  { left: 292px; top: 637px; background: var(--paper); }

  .front-mark {
    position: absolute; left: 262px; top: 28px;
    width: 296px; height: 296px; border-radius: 50%;
    background: var(--sky);
  }
  .front-name {
    position: absolute; left: 28px; top: 260px;
    color: var(--white); font-weight: 600; font-size: 22px; letter-spacing: 0.5px;
  }

  .back-wave { position: absolute; left: 0; top: 0; width: 594px; height: 130px; }
  .person { position: absolute; right: 44px; top: 26px; text-align: right; }
  .person-name { color: var(--sky); font-weight: 600; font-size: 24px; letter-spacing: 0.5px; }
  .person-title { color: var(--white); font-size: 15px; margin-top: 2px; }

  .brand { position: absolute; left: 38px; top: 128px; display: flex; align-items: center; gap: 16px; }
  .brand-dot { width: 70px; height: 70px; border-radius: 50%; background: var(--sky); }
  .brand-name { color: var(--ink); font-weight: 600; font-size: 24px; letter-spacing: 0.5px; }

  .contact { position: absolute; list-style: none; color: var(--ink); font-size: 15.5px; }
  .contact li { display: flex; align-items: center; height: 21.5px; }
  .contact svg { width: 13px; height: 13px; margin-right: 14px; flex: none; }
  .contact-lines { left: 46px; top: 247px; }
  .contact-address { left: 334px; top: 268px; }
  .contact-address li { padding-left: 0; }
  .contact-address .indent { padding-left: 27px; }
</style>
</head>
<body>

<section class="card card-front">
  <div class="front-mark"></div>
  <p class="front-name">CREWLINE HEALTH</p>
</section>

<section class="card card-back">
  <svg class="back-wave" viewBox="0 0 594 130">
    <path d="M0 0 H594 V92 C520 112 440 70 330 52 C240 38 120 42 0 62 Z" fill="var(--navy)"/>
    <path d="M0 58 C110 34 210 28 300 42 C200 34 110 42 0 66 Z" fill="var(--sky)"/>
    <path d="M55 62 C180 30 290 60 390 88 C470 110 540 104 594 88" fill="none" stroke="var(--amber)" stroke-width="4"/>
  </svg>
  <div class="person">
    <p class="person-name">DAN MARLOW</p>
    <p class="person-title">Senior Doctor</p>
  </div>

  <div class="brand">
    <div class="brand-dot"></div>
    <p class="brand-name">CREWLINE HEALTH</p>
  </div>

  <ul class="contact contact-lines">
    <li>
      <svg viewBox="0 0 16 16"><path d="M3 2h3l1.5 4-2 1.2a9 9 0 0 0 3.3 3.3L10 8.5l4 1.5v3a1.5 1.5 0 0 1-1.5 1.5A11.5 11.5 0 0 1 1.5 3.5 1.5 1.5 0 0 1 3 2z" fill="var(--sky)"/></svg>
      555-210-4478
    </li>
    <li>
      <svg viewBox="0 0 16 16"><rect x="1" y="3" width="14" height="10" fill="var(--ink)"/><path d="M1 3l7 6 7-6" fill="none" stroke="var(--paper)" stroke-width="1.4"/></svg>
      dan@crewlinehealth.com
    </li>
    <li>
      <svg viewBox="0 0 16 16"><circle cx="8" cy="8" r="6.5" fill="none" stroke="var(--amber)" stroke-width="1.5"/><path d="M1.5 8h13M8 1.5c-3 3.5-3 9.5 0 13M8 1.5c3 3.5 3 9.5 0 13" fill="none" stroke="var(--amber)" stroke-width="1.2"/></svg>
      www.crewlinehealth.com
    </li>
  </ul>

  <ul class="contact contact-address">
    <li>
      <svg viewBox="0 0 16 16"><path d="M8 1a5 5 0 0 0-5 5c0 4 5 9 5 9s5-5 5-9a5 5 0 0 0-5-5z" fill="var(--amber)"/><circle cx="8" cy="6" r="1.8" fill="var(--paper)"/></svg>
      48 Harbor Way, Suite 210
    </li>
    <li class="indent">Bayport, State 40210</li>
  </ul>
</section>

</body>
</html>
```